Full Page Magazine Add for Bulb Recycler

We need ad that to promote our expertise, capabilities and value in industry trade magazines. We want clean, clear look feel to reflect our impact on the environment.

Target Market(s)

Industry -- Electricians -- Environmental Services

Font styles to use
Sans Serif

Colors
eef8f9

Requirements
Must have
• I have included instructions outlining all details of must / haves -- ALSO) there are 4 jpegs of LOOK/FEEL Examples that we like -- as reference -- FILE names are EXAMPLE
Nice to have
• Welcome guidance on helping with logo transition -- we're moving from Halvern Supplies -- to Tally by the Brook -- but for now -- need to display both -- we've just put an IS in between -- but if you have ideas definitely WELCOME

```html
<!DOCTYPE html>
<html lang="en">
<head>
<meta charset="utf-8">
<title>Halvern Supplies – Protecting the Environment</title>
<link rel="stylesheet" href="https://fonts.googleapis.com/css2?family=Jost:wght@500;600&family=Didact+Gothic&display=swap">
<style>
  :root {
    --page: #f1f2f4;
    --brand-blue: #1b4f9c;
    --deep-blue: #1d3f8a;
    --brand-green: #3daf63;
    --soft-green: #8fd09b;
    --lime: #c9e27a;
    --ink: #2f2f33;
    --body-ink: #3d3d42;
  }
  * { margin: 0; padding: 0; box-sizing: border-box; }
  html, body { width: 927px; height: 1200px; overflow: hidden; background: var(--page); }
  .ad {
    position: relative; width: 927px; height: 1200px; overflow: hidden;
    background: var(--page); font-family: "Didact Gothic", sans-serif; color: var(--body-ink);
  }
  .band { position: absolute; left: 0; width: 927px; }
  .band--top { top: 0; height: 160px; }
  .band--bottom { bottom: 0; height: 140px; }

  .headline { position: absolute; top: 162px; left: 0; width: 927px; text-align: center; }
  .headline__main {
    font-family: "Jost", sans-serif; font-weight: 600; font-size: 56px; line-height: 1;
    color: var(--brand-blue); letter-spacing: -0.2px;
  }
  .headline__sub {
    font-family: "Jost", sans-serif; font-weight: 500; font-size: 38px; line-height: 1;
    color: var(--ink); margin-top: 4px;
  }

  .feature { position: absolute; width: 266px; }
  .feature__photo { display: block; width: 266px; }
  .feature__label {
    position: absolute; left: 0; width: 266px; color: #fff;
    font-family: "Jost", sans-serif; font-weight: 500; line-height: 1;
    display: flex; flex-direction: column; justify-content: center;
  }
  .feature__label--green { background: var(--brand-green); }
  .feature__label--blue { background: var(--deep-blue); }
  .feature__text {
    position: absolute; left: 4px; width: 258px;
    font-size: 15.2px; line-height: 18.2px; text-align: justify;
  }

  .service-map { position: absolute; left: 607px; top: 655px; width: 300px; }
  .service-map__title {
    font-family: "Jost", sans-serif; font-weight: 600; font-size: 24px; color: var(--ink);
    text-align: center; line-height: 1;
  }
  .service-map__sub {
    font-family: "Jost", sans-serif; font-weight: 500; font-size: 17px; color: var(--ink);
    text-align: center; margin-top: 4px;
  }
  .service-map__art { margin-top: 10px; display: block; }

  .brand { position: absolute; left: 622px; top: 918px; width: 268px; }
  .brand__current { display: flex; align-items: center; gap: 10px; }
  .brand__dot { width: 84px; height: 84px; border-radius: 50%; background: var(--brand-blue); flex: none; }
  .brand__name {
    font-family: "Jost", sans-serif; font-weight: 600; font-size: 38px; line-height: 0.95;
    color: var(--brand-blue);
  }
  .brand__transition { display: flex; align-items: center; gap: 10px; margin-top: 20px; }
  .brand__is { font-family: "Jost", sans-serif; font-weight: 600; font-size: 24px; color: var(--brand-blue); }
  .brand__square { width: 30px; height: 30px; background: var(--brand-green); flex: none; }
  .brand__next {
    font-family: "Jost", sans-serif; font-weight: 600; font-size: 24px; line-height: 1;
    color: var(--brand-green);
  }
  .brand__web {
    position: absolute; left: 0; top: 165px; width: 268px; text-align: center;
    font-family: "Jost", sans-serif; font-weight: 600; font-size: 20px; color: var(--brand-blue);
  }
</style>
</head>
<body>
<main class="ad">

  <svg class="band band--top" viewBox="0 0 927 160" preserveAspectRatio="none" aria-hidden="true">
    <defs>
      <linearGradient id="topGreen" x1="0" x2="1" y1="0" y2="0">
        <stop offset="0" stop-color="#3daf63"/>
        <stop offset="1" stop-color="#a5d9a8"/>
      </linearGradient>
    </defs>
    <polygon points="0,0 927,0 927,50 463,75 0,20" fill="#1d3f8a"/>
    <polygon points="0,30 463,85 927,30 927,70 463,155 0,95" fill="url(#topGreen)"/>
    <polygon points="0,40 300,85 463,95 240,78 0,55" fill="#c9e27a"/>
    <polygon points="560,82 927,20 927,38 620,86" fill="#c9e27a"/>
  </svg>

  <header class="headline">
    <h1 class="headline__main">Protecting the Environment</h1>
    <p class="headline__sub">and Assuring Your Compliance</p>
  </header>

  <section class="feature" style="left:54px; top:272px;">
    <svg class="feature__photo" width="266" height="174" role="img" aria-label="Photo of workers at a bulb recycling processing line">
      <defs><linearGradient id="g1" x1="0" y1="0" x2="0" y2="1"><stop offset="0" stop-color="#8a97a6"/><stop offset="1" stop-color="#4d5660"/></linearGradient></defs>
      <rect width="266" height="174" fill="url(#g1)"/>
    </svg>
    <h2 class="feature__label feature__label--green" style="top:174px; height:55px; font-size:33px; align-items:center;">Technology</h2>
    <p class="feature__text" style="top:236px;">Our processing facilities are equipped with the most advanced recycling equipment in the industry. We safely recycle millions of bulbs every year.</p>
  </section>

  <section class="feature" style="left:331px; top:272px;">
    <svg class="feature__photo" width="266" height="157" role="img" aria-label="Photo of a pile of used fluorescent tubes">
      <defs><linearGradient id="g2" x1="0" y1="0" x2="1" y2="1"><stop offset="0" stop-color="#f4f4f2"/><stop offset="1" stop-color="#c8cbcc"/></linearGradient></defs>
      <rect width="266" height="157" fill="url(#g2)"/>
    </svg>
    <h2 class="feature__label feature__label--blue" style="top:157px; height:72px; font-size:32px; padding-left:42px;">Reclaiming<br>Resources</h2>
    <p class="feature__text" style="top:234px;">We separate and produce clean glass, plastic and metals for re-use. In our high temp retort ovens, we remove mercury from phosphor powder and produce virgin-quality mercury for use in research. Clean powder is further processed to extract rare-earth metals for use in manufacturing.</p>
  </section>

  <section class="feature" style="left:608px; top:272px;">
    <svg class="feature__photo" width="266" height="174" role="img" aria-label="Photo of a white box truck used for waste pickup">
      <defs><linearGradient id="g3" x1="0" y1="0" x2="0" y2="1"><stop offset="0" stop-color="#e3e4e6"/><stop offset="1" stop-color="#a9abae"/></linearGradient></defs>
      <rect width="266" height="174" fill="url(#g3)"/>
    </svg>
    <h2 class="feature__label feature__label--green" style="top:174px; height:55px; font-size:33px; align-items:center;">Nationwide</h2>
    <p class="feature__text" style="top:234px;">We provide processing and licensed pick up of hazardous and universal waste by pallet-full or truck load for many of the largest and most well-known companies, institutions and agencies in the country.</p>
  </section>

  <section class="service-map">
    <h3 class="service-map__title">Nationwide Service</h3>
    <p class="service-map__sub">by Pallet-full or Truckload</p>
    <svg class="service-map__art" width="300" height="190" role="img" aria-label="Map of the United States marking service locations">
      <rect x="0" y="0" width="300" height="190" rx="14" fill="#c9cbcf"/>
    </svg>
  </section>

  <section class="feature" style="left:54px; top:687px;">
    <svg class="feature__photo" width="266" height="151" role="img" aria-label="Close-up photo of colorful batteries">
      <defs><linearGradient id="g4" x1="0" y1="0" x2="1" y2="0"><stop offset="0" stop-color="#8fb9c8"/><stop offset="0.5" stop-color="#e06a3f"/><stop offset="1" stop-color="#9c7fc1"/></linearGradient></defs>
      <rect width="266" height="151" fill="url(#g4)"/>
    </svg>
    <h2 class="feature__label feature__label--blue" style="top:151px; height:80px; font-size:31px; align-items:center; text-align:center;">Fast Easy<br>Mail-In Recycling</h2>
    <p class="feature__text" style="top:238px;">Tally by the Brook Recycling kits ensure you have what you need when you need to properly manage your batteries, bulbs, ballasts, exit signs and more. Pre-paid shipping and processing for bulbs, batteries, ballasts, exit signs and more, shipped to you within 24 hours.</p>
  </section>

  <section class="feature" style="left:331px; top:687px;">
    <svg class="feature__photo" width="266" height="151" role="img" aria-label="Photo of red and green exit signs">
      <defs><linearGradient id="g5" x1="0" y1="0" x2="1" y2="1"><stop offset="0" stop-color="#e8e9ea"/><stop offset="0.55" stop-color="#d8d9db"/><stop offset="1" stop-color="#c9cbcd"/></linearGradient></defs>
      <rect width="266" height="151" fill="url(#g5)"/>
    </svg>
    <h2 class="feature__label feature__label--green" style="top:151px; height:80px; font-size:31px; align-items:center; text-align:center;">Egress<br>Safety Solutions</h2>
    <p class="feature__text" style="top:238px;">We are your single source for upgrading exit safety. In addition to fully-managed retrofit and tritium exit sign recycling, we offer a complete line of energy and maintenance-free phosphorescent exit signs and safety marking.</p>
  </section>

  <svg class="band band--bottom" viewBox="0 0 927 140" preserveAspectRatio="none" aria-hidden="true">
    <defs>
      <linearGradient id="botGreen" x1="0" x2="1" y1="0" y2="0">
        <stop offset="0" stop-color="#3daf63"/>
        <stop offset="1" stop-color="#a5d9a8"/>
      </linearGradient>
    </defs>
    <polygon points="0,70 315,10 927,120 927,140 0,140" fill="url(#botGreen)"/>
    <polygon points="0,90 315,40 927,130 927,140 0,140" fill="#c9e27a"/>
    <polygon points="0,108 315,65 927,140 0,140" fill="#1d3f8a"/>
  </svg>

  <section class="brand">
    <div class="brand__current">
      <span class="brand__dot"></span>
      <span class="brand__name">Halvern<br>Supplies</span>
    </div>
    <div class="brand__transition">
      <span class="brand__is">IS</span>
      <span class="brand__square"></span>
      <span class="brand__next">Tally by the Brook</span>
    </div>
    <p class="brand__web">www.tallybythebrook.com</p>
  </section>

</main>
</body>
</html>
```